VELMOR Website Design

We need a website designed for our company VELMOR. We are a luxury lifestyle club that will provide benefits and services for our members. The site should be clean & sleek, preferably using black and white (or darker colors). (example sites: stravenhall.example, plinth.example)

Here is a link of a sample page I did using wix. (https://dunmere7.sitehostly.example/mysite) This can be used to get a general idea.

Target Market(s)

Upper Middle Class in the United States

Number of Pages Required

5+ page

Font styles to use
Sans Serif
Other font styles liked:
• Arial (or other similar fonts)

Requirements
Must have
• A clean design that is eye-catching and speaks to our company.
Nice to have
• Ideas for copy.

```html
<!DOCTYPE html>
<html lang="en">
<head>
<meta charset="utf-8">
<title>VELMOR — Lifestyle Club</title>
<link rel="stylesheet" href="https://fonts.googleapis.com/css2?family=Montserrat:wght@400;500;600;700&family=Open+Sans:ital,wght@0,400;0,600;1,400;1,600&display=swap">
<style>
:root{
  --bg:#232323;
  --bg-deep:#1c1c1c;
  --band:#2a2a2a;
  --card:#1a1a1a;
  --blue:#0b5fe8;
  --white:#ffffff;
  --muted:#bdbdbd;
  --line:#3a3a3a;
}
*{margin:0;padding:0;box-sizing:border-box}
html,body{width:1200px;height:3442px;overflow:hidden}
body{background:var(--bg);color:var(--white);font-family:"Open Sans",Arial,sans-serif;position:relative}
.abs{position:absolute}
.heading{font-family:"Montserrat",Arial,sans-serif;font-weight:500;letter-spacing:1px;text-transform:uppercase}

/* hero */
.hero{left:0;top:0;width:1200px;height:654px;background:linear-gradient(180deg,#2b2d33 0%,#1e1c22 55%,#151515 100%)}
.hero-photo{left:0;top:0;width:1200px;height:654px;background:radial-gradient(ellipse at 50% 30%,rgba(120,70,80,.35),rgba(20,20,24,0) 65%)}
.brand{left:118px;top:22px;width:196px;height:48px;border:2px solid var(--white);font-family:"Montserrat",Arial,sans-serif;font-weight:600;font-size:34px;line-height:44px;text-align:center;letter-spacing:2px}
.nav{right:160px;top:36px;display:flex;gap:26px;font-size:13px;font-weight:600}
.search{left:1058px;top:34px;width:22px;height:22px;border-radius:50%;background:var(--blue)}
.hero-title{left:120px;top:312px;font-size:41px;line-height:62px;font-weight:600;letter-spacing:1.5px}
.arrow-l{left:38px;top:326px}
.arrow-r{left:1128px;top:326px}
.dots{left:572px;top:578px;display:flex;gap:8px}
.dots span{width:10px;height:10px;border-radius:50%;background:var(--white)}
.dots span.on{background:var(--blue)}
.notch{left:562px;top:620px}

/* about */
.about-band{left:0;top:654px;width:1200px;height:103px;background:var(--band)}
.section-title{width:1200px;text-align:center;font-size:38px}
.tabs{left:0;top:757px;width:1200px;height:51px;background:var(--bg-deep)}
.tab-list{left:110px;top:757px;display:flex;height:51px}
.tab-list div{padding:0 28px;border-left:1px solid var(--line);font-size:11px;line-height:51px}
.tab-list div:last-child{border-right:1px solid var(--line)}
.about-photo{left:110px;top:863px;width:475px;height:161px;background:linear-gradient(180deg,#3a5a9a 0%,#b78a5a 60%,#3f5a2e 100%)}
.club-title{left:110px;top:1044px;font-size:26px;font-weight:500}
.club-text{left:110px;top:1090px;width:470px;font-size:11px;line-height:20px;color:var(--muted)}
.feature-icon{width:58px;height:58px;border-radius:50%;background:var(--blue)}
.feature-label{left:695px;font-family:"Montserrat",Arial,sans-serif;font-size:10px;font-weight:600;color:var(--blue);text-transform:uppercase}
.feature-text{left:695px;width:390px;font-size:10.5px;line-height:20px;color:var(--muted)}

/* team */
.team{left:0;top:1267px;width:1200px;height:941px;background:var(--bg)}
.subtitle{width:1200px;text-align:center;font-style:italic;font-weight:600;font-size:19px}
.card{width:310px;height:349px;background:var(--card)}
.card.active{background:var(--blue)}
.card .photo{position:absolute;left:0;top:0;width:310px;height:207px;background:linear-gradient(180deg,#4a4a4a,#2a2a2a)}
.card.active .photo{height:150px}
.card .pin{position:absolute;left:126px;top:178px;width:58px;height:58px;border-radius:50%;background:var(--blue)}
.card.active .pin{top:121px}
.card .name{position:absolute;left:0;top:242px;width:310px;text-align:center;font-family:"Montserrat",Arial,sans-serif;font-size:14px;font-weight:500;letter-spacing:.5px;text-transform:uppercase}
.card.active .name{top:187px}
.card .rule{position:absolute;left:130px;top:264px;width:50px;height:1px;background:var(--white)}
.card.active .rule{top:209px}
.card .bio{position:absolute;left:28px;top:276px;width:254px;text-align:center;font-size:10.5px;line-height:20px;font-weight:600}
.card.active .bio{top:222px}
.card .social{position:absolute;left:95px;top:300px;display:flex;gap:8px}
.card .social span{width:30px;height:30px;border:1.5px solid var(--white);border-radius:50%}

/* cta */
.cta{left:0;top:2208px;width:1200px;height:454px;background:linear-gradient(180deg,#2c3a40 0%,#24343a 50%,#1f2a2e 100%)}
.cta-shade{left:0;top:2208px;width:1200px;height:454px;background:rgba(10,12,14,.55)}
.cta-title{width:1200px;text-align:center;font-size:30px;font-weight:600;line-height:42px;letter-spacing:2px}
.btn{left:544px;top:2470px;width:112px;height:38px;border:2px solid var(--white);font-size:12px;line-height:34px;text-align:center;letter-spacing:1px}

/* testimonials */
.testimonial{left:0;top:2814px;width:1200px;height:388px;background:var(--card)}
.testi-photo{left:0;top:2814px;width:379px;height:289px;background:linear-gradient(180deg,#c9d6e2 0%,#7a8fa0 45%,#5b4532 100%)}
.testi-role{top:3103px;width:379px;height:99px}
.testi-role.active{background:var(--blue)}
.role-name{width:379px;text-align:center;font-size:10px;color:var(--muted);font-weight:600;text-transform:uppercase}
.role-title{width:379px;text-align:center;font-family:"Montserrat",Arial,sans-serif;font-size:25px;font-weight:500;text-transform:uppercase;letter-spacing:1px}
.testi-text{left:402px;top:2848px;width:770px;font-size:19px;line-height:40px}

/* footer */
.footer{left:0;top:3202px;width:1200px;height:199px;background:var(--bg)}
.foot-small{font-size:10px;line-height:18px;color:var(--white)}
.foot-head{font-size:11px;color:var(--blue);font-weight:600}
.foot-social{left:110px;top:3305px;display:flex;gap:10px}
.foot-social span{width:28px;height:28px;border:1.5px solid #888;border-radius:50%}
.email-field{left:778px;top:3344px;width:146px;height:26px;border:1px solid #666;border-radius:13px;font-size:10px;line-height:24px;padding-left:12px;color:#999}
.bottom-bar{left:0;top:3401px;width:1200px;height:41px;background:var(--bg-deep)}
</style>
</head>
<body>

<!-- Hero -->
<div class="abs hero"></div>
<div class="abs hero-photo" role="img" aria-label="Photo of performers bowing on a stage before an audience"></div>
<div class="abs brand">VELMOR</div>
<nav class="abs nav"><span>About us</span><span>Services &amp; Benefits</span><span>Contact</span></nav>
<svg class="abs" style="left:1058px;top:34px" width="22" height="22" viewBox="0 0 22 22"><circle cx="11" cy="11" r="11" fill="#0b5fe8"/><circle cx="10" cy="10" r="4" fill="none" stroke="#fff" stroke-width="1.6"/><line x1="13" y1="13" x2="16" y2="16" stroke="#fff" stroke-width="1.6"/></svg>
<h1 class="abs heading hero-title">Memberships for creatives, athletes,<br>artists, and other professionals.</h1>
<svg class="abs arrow-l" width="24" height="36" viewBox="0 0 24 36"><polyline points="18,4 6,18 18,32" fill="none" stroke="#fff" stroke-width="4"/></svg>
<svg class="abs arrow-r" width="24" height="36" viewBox="0 0 24 36"><polyline points="6,4 18,18 6,32" fill="none" stroke="#fff" stroke-width="4"/></svg>
<div class="abs dots"><span class="on"></span><span></span><span></span></div>
<svg class="abs notch" width="76" height="34" viewBox="0 0 76 34"><polygon points="0,34 38,0 76,34" fill="#0b5fe8"/><polyline points="28,20 38,12 48,20" fill="none" stroke="#fff" stroke-width="2"/></svg>

<!-- About -->
<div class="abs about-band"></div>
<h2 class="abs heading section-title" style="left:0;top:680px">About us</h2>
<div class="abs tabs"></div>
<div class="abs tab-list"><div>Services</div><div>Experiences</div><div>About VELMOR</div></div>
<div class="abs about-photo" role="img" aria-label="Photo of a lit luxury villa with gardens at dusk"></div>
<h3 class="abs heading club-title">Lifestyle club</h3>
<p class="abs club-text">Lorem ipsum dolor sit amet, consectetur adipiscing elit. Aenean egestas eu leo nec eleifend. Nulla sapien turpis, convallis ac ultrices sed, aliquam sit amet arcu. Phasellus est orci, bibendum consequat quam sit amet, facilisis pharetra nisl. Nullam ultrices mi quam, et volutpat magna suscipit eget.</p>

<svg class="abs" style="left:614px;top:857px" width="58" height="58" viewBox="0 0 58 58"><circle cx="29" cy="29" r="29" fill="#0b5fe8"/><polyline points="20,33 29,24 38,33" fill="none" stroke="#fff" stroke-width="4"/></svg>
<div class="abs feature-label" style="top:864px">Benefits and services</div>
<p class="abs feature-text" style="top:880px">VELMOR membership provides you with amazing benefits and services.</p>

<svg class="abs" style="left:614px;top:995px" width="58" height="58" viewBox="0 0 58 58"><circle cx="29" cy="29" r="29" fill="#0b5fe8"/><polyline points="20,33 29,24 38,33" fill="none" stroke="#fff" stroke-width="4"/></svg>
<div class="abs feature-label" style="top:998px">Experiences</div>
<p class="abs feature-text" style="top:1014px">VELMOR organizes and supports a ton of private events and parties for our members.</p>

<svg class="abs" style="left:614px;top:1119px" width="58" height="58" viewBox="0 0 58 58"><circle cx="29" cy="29" r="29" fill="#0b5fe8"/><polyline points="20,33 29,24 38,33" fill="none" stroke="#fff" stroke-width="4"/></svg>
<div class="abs feature-label" style="top:1126px">About VELMOR</div>
<p class="abs feature-text" style="top:1142px">VELMOR is a members only lifestyle club founded in order to bring the best services, experiences, and opportunities to our diverse community of members.</p>

<!-- Team -->
<div class="abs team"></div>
<h2 class="abs heading section-title" style="left:0;top:1298px">Our team</h2>
<p class="abs subtitle" style="left:0;top:1356px">Morbi leo risus, porta ac consectetur ac, vestibulum at eros.</p>

<div class="abs card" style="left:110px;top:1423px"><div class="photo" role="img" aria-label="Portrait of team member Aldo Verrin"></div><div class="pin"></div><svg style="position:absolute;left:126px;top:178px" width="58" height="58" viewBox="0 0 58 58"><polyline points="20,33 29,24 38,33" fill="none" stroke="#fff" stroke-width="4"/></svg><div class="name">Aldo Verrin</div><div class="rule"></div><p class="bio">Morbi leo risus, porta ac consectetur ac, vestibulum at eros. Lorem ipsum dolor sit amet, consectetur adipiscing elit.</p></div>

<div class="abs card active" style="left:445px;top:1423px"><div class="photo" role="img" aria-label="Portrait of team member Tomas Hale"></div><div class="pin"></div><svg style="position:absolute;left:126px;top:121px" width="58" height="58" viewBox="0 0 58 58"><polyline points="20,33 29,24 38,33" fill="none" stroke="#fff" stroke-width="4"/></svg><div class="name">Tomas Hale</div><div class="rule"></div><p class="bio">Morbi leo risus, porta ac consectetur ac, vestibulum at eros. Lorem ipsum dolor sit amet, consectetur adipiscing elit.</p><div class="social"><span></span><span></span><span></span></div></div>

<div class="abs card" style="left:778px;top:1423px"><div class="photo" role="img" aria-label="Portrait of team member Renna Solis"></div><div class="pin"></div><svg style="position:absolute;left:126px;top:178px" width="58" height="58" viewBox="0 0 58 58"><polyline points="20,33 29,24 38,33" fill="none" stroke="#fff" stroke-width="4"/></svg><div class="name">Renna Solis</div><div class="rule"></div><p class="bio">Morbi leo risus, porta ac consectetur ac, vestibulum at eros. Lorem ipsum dolor sit amet, consectetur adipiscing elit.</p></div>

<div class="abs card" style="left:110px;top:1795px"><div class="photo" role="img" aria-label="Portrait of team member Marco Dellin"></div><div class="pin"></div><svg style="position:absolute;left:126px;top:178px" width="58" height="58" viewBox="0 0 58 58"><polyline points="20,33 29,24 38,33" fill="none" stroke="#fff" stroke-width="4"/></svg><div class="name">Marco Dellin</div><div class="rule"></div><p class="bio">Morbi leo risus, porta ac consectetur ac, vestibulum at eros. Lorem ipsum dolor sit amet, consectetur adipiscing elit.</p></div>

<div class="abs card" style="left:445px;top:1795px"><div class="photo" role="img" aria-label="Portrait of team member Ilsa Varnova"></div><div class="pin"></div><svg style="position:absolute;left:126px;top:178px" width="58" height="58" viewBox="0 0 58 58"><polyline points="20,33 29,24 38,33" fill="none" stroke="#fff" stroke-width="4"/></svg><div class="name">Ilsa Varnova</div><div class="rule"></div><p class="bio">Morbi leo risus, porta ac consectetur ac, vestibulum at eros. Lorem ipsum dolor sit amet, consectetur adipiscing elit.</p></div>

<div class="abs card" style="left:778px;top:1795px"><div class="photo" role="img" aria-label="Portrait of team member Corinne Pell"></div><div class="pin"></div><svg style="position:absolute;left:126px;top:178px" width="58" height="58" viewBox="0 0 58 58"><polyline points="20,33 29,24 38,33" fill="none" stroke="#fff" stroke-width="4"/></svg><div class="name">Corinne Pell</div><div class="rule"></div><p class="bio">Morbi leo risus, porta ac consectetur ac, vestibulum at eros. Lorem ipsum dolor sit amet, consectetur adipiscing elit.</p></div>

<!-- Call to action -->
<div class="abs cta" role="img" aria-label="Photo of a resort pool terrace overlooking the sea"></div>
<div class="abs cta-shade"></div>
<h2 class="abs heading cta-title" style="left:0;top:2320px">VELMOR<br>Membership provides you with amazing benefits and<br>services.</h2>
<div class="abs btn">VISIT</div>

<!-- Testimonials -->
<h2 class="abs heading section-title" style="left:0;top:2692px;font-size:31px">Testimonials</h2>
<p class="abs subtitle" style="left:0;top:2744px">Dummy text of the printing and typesetting</p>
<div class="abs testimonial"></div>
<div class="abs testi-photo" role="img" aria-label="Photo of a yacht deck at sunset on the sea"></div>
<p class="abs testi-text">Lorem Ipsum is simply dummy text of the printing and typesetting industry. Lorem Ipsum has been the industry's standard dummy text ever since the 1500s, when an unknown printer took a galley of type and scrambled it to make a type specimen book. It has survived not only five centuries, but also the leap into electronic typesetting, remaining.</p>
<div class="abs testi-role active" style="left:0"></div>
<div class="abs role-name" style="left:0;top:3127px">Evan Throsby</div>
<div class="abs role-title" style="left:0;top:3146px">Co-founder</div>
<div class="abs role-name" style="left:362px;top:3127px">Nadia Corwell</div>
<div class="abs role-title" style="left:362px;top:3146px">Founder</div>
<div class="abs role-name" style="left:697px;top:3127px">Owen Harlice</div>
<div class="abs role-title" style="left:697px;top:3146px">Manager</div>

<!-- Footer -->
<div class="abs footer"></div>
<p class="abs foot-small" style="left:110px;top:3262px;font-weight:600">Copyright 2017–18 <span style="color:var(--blue)">VELMOR</span><br>Designed and developed by VELMOR Studio</p>
<div class="abs foot-social"><span></span><span></span><span></span><span></span></div>
<div class="abs foot-head" style="left:443px;top:3262px">Our location</div>
<p class="abs foot-small" style="left:443px;top:3290px">Northgate Holdings LLC 48 Ashby Row,<br>Suite 12 Fernvale, IL 00000<br>Phone : +00 1 98765432<br>Email : info@velmor.example</p>
<div class="abs foot-head" style="left:778px;top:3262px">Keep in touch</div>
<p class="abs foot-small" style="left:778px;top:3282px;width:320px">Lorem ipsum dolor sit amet, consectetur adi sollicitud ante tellus ornare mi, et mollis</p>
<div class="abs email-field">Your email</div>
<svg class="abs" style="left:900px;top:3351px" width="12" height="12" viewBox="0 0 12 12"><polyline points="2,6 10,6 6,2 10,6 6,10" fill="none" stroke="#aaa" stroke-width="1.4"/></svg>
<div class="abs bottom-bar"></div>
<svg class="abs" style="left:590px;top:3414px" width="20" height="14" viewBox="0 0 20 14"><polyline points="3,11 10,4 17,11" fill="none" stroke="#fff" stroke-width="3"/></svg>

</body>
</html>
```